Recruitment Agency in Texas, needs a stand out header letter

Our colours are red and grey and can be found on our website
just my logo will be sufficient and address...

Target Market(s)

Engineering Manufacturing

Colors
0094D4
00A9DD
6FCCEA
C7EBF8
E9F6FB
EB3D1F
EC4F4E
F09395
F8D3D4
FCEDEE

Requirements
Must have
• use colors red and grey
Should not have
• Please use same colors and font as my logo. My website is keltrayrecruitment.com

```html
<!DOCTYPE html>
<html lang="en">
<head>
<meta charset="utf-8">
<title>Keltray Recruitment Letterhead</title>
<link rel="stylesheet" href="https://fonts.googleapis.com/css2?family=Arimo:wght@400;700&display=swap">
<style>
  :root {
    --backdrop: #d9dadc;
    --paper: #eeeeef;
    --paper-shade: #e6e7e8;
    --brand-red: #d3202a;
    --brand-grey: #5d5e61;
    --ink: #4a4b4e;
    --ink-soft: #55565a;
  }
  * { box-sizing: border-box; margin: 0; padding: 0; }
  html, body {
    width: 1200px; height: 1141px; overflow: hidden;
    background: var(--backdrop);
    font-family: "Arimo", Arial, sans-serif;
  }
  .letterhead {
    position: absolute; left: 262px; top: 96px;
    width: 675px; height: 948px;
    background: linear-gradient(160deg, var(--paper) 0%, var(--paper-shade) 100%);
    box-shadow: 0 2px 6px rgba(0,0,0,0.18);
  }
  .brand-name {
    position: absolute; left: 48px; top: 76px;
    font-weight: 700; font-size: 27px; letter-spacing: -0.8px;
    color: var(--brand-red);
  }
  .office {
    position: absolute; left: 479px; top: 48px;
    font-size: 9.8px; line-height: 12px; color: var(--ink-soft);
  }
  .office-address { margin-bottom: 8px; }
  .contact-list { list-style: none; }
  .contact-list li { display: flex; align-items: center; gap: 6px; height: 12px; }
  .contact-list svg { width: 8px; height: 8px; fill: var(--brand-red); flex: none; }
  .salutation {
    position: absolute; left: 51px; top: 236px;
    font-size: 16px; color: var(--ink);
  }
  .letter-body {
    position: absolute; left: 51px; top: 284px; width: 575px;
    font-size: 9.7px; line-height: 14.5px; color: var(--ink);
    text-align: justify;
  }
  .letter-body p { margin-bottom: 14px; }
  .closing {
    position: absolute; left: 51px; top: 601px;
    font-size: 9.7px; color: var(--ink);
  }
  .signature {
    position: absolute; left: 46px; top: 636px; width: 196px; height: 52px;
    background: linear-gradient(90deg, rgba(40,40,45,0.12), rgba(40,40,45,0.05));
    border-radius: 4px;
  }
  .footer-band {
    position: absolute; left: 0; bottom: 0; width: 100%; height: 14px;
    display: flex; gap: 3px;
  }
  .footer-band-red { width: 479px; background: var(--brand-red); }
  .footer-band-grey { flex: 1; background: var(--brand-grey); }
</style>
</head>
<body>
<main class="letterhead">
  <div class="brand-name">KeltrayRecruitment</div>

  <address class="office" style="font-style:normal">
    <div class="office-address">Houston Office<br>48 Brookfield Plaza Houston,</div>
    <ul class="contact-list">
      <li><svg viewBox="0 0 16 16"><path d="M3 1l3 0 1 4-2 1.5c1 2 2.5 3.5 4.5 4.5L11 9l4 1v3c0 1-1 2-2 2C7 15 1 9 1 3c0-1 1-2 2-2z"/></svg>(+1) 713-555-0148</li>
      <li><svg viewBox="0 0 16 16"><path d="M4 1h8v4H4zM1 6h14v6h-3v3H4v-3H1zM5 10v3h6v-3z"/></svg>713-555-0149</li>
      <li><svg viewBox="0 0 16 16"><path d="M1 3h14v10H1zM2.5 4.5L8 9l5.5-4.5v-0.5h-11z" fill-rule="evenodd"/></svg>info@keltrayrecruitment.com</li>
      <li><svg viewBox="0 0 16 16"><circle cx="8" cy="8" r="7"/></svg>www.keltrayrecruitment.com</li>
    </ul>
  </address>

  <h1 class="salutation" style="font-weight:400">Dear Mr. Smith,</h1>

  <section class="letter-body">
    <p>Lorem ipsum dolor sit amet, consectetur adipiscing elit. Donec orci purus, luctus vitae dignissim eu, iaculis sed purus. Vivamus faucibus, ipsum nec aliquet viverra, leo mauris condimentum ligula, sit amet sagittis enim ligula quis arcu. Nam egestas tortor id nisi porttitor mattis. In tortor ante, ultricies in suscipit a, tempus non massa. Vivamus et auctor mi. Fusce vel massa nulla. Phasellus nec eros mauris, et scelerisque orci.</p>
    <p>Donec malesuada orci vitae nulla accumsan porta a id massa. Quisque accumsan iaculis magna sit amet fringilla. Maecenas consequat, magna eget tincidunt semper, odio nibh rutrum mi, id feugiat ante nisi eu risus. Vestibulum nunc orci, rhoncus a placerat in, ultricies in mi. Cras mattis varius eros, vel fringilla nisi suscipit eget. Quisque scelerisque sagittis nulla at porttitor.</p>
    <p>Sed id augue vitae urna euismod commodo aliquet a quam. Pellentesque arcu velit, cursus et malesuada ut, consequat et diam. Nullam erat sem, rhoncus id ullamcorper vitae, rhoncus et arcu. In ultricies ultricies nulla, ut rutrum nisi iaculis at. Donec eu magna a metus ornare faucibus. Fusce aliquet faucibus ultricies. Morbi semper, est id tincidunt gravida, sem arcu adipiscing lacus, ac bibendum nulla leo eu purus. Quisque nec diam sed risus consectetur accumsan quis quis nibh. Vestibulum id purus lorem.</p>
    <p>It is a long established fact that a reader will be distracted by the readable content of a page when looking at its layout. The point of using Lorem Ipsum is that it has a more-or-less normal distribution of letters, as opposed to using 'Content here, content here', making it look like readable English. Many desktop publishing packages</p>
    <p>ada ut, consequat et diam. Nullam erat sem, rhoncus id ullamcorper vitae, rhoncus et arcu. In ultricies ultricies nulla, ut rutrum nisi iaculis at. Donec eu magna a metus ornare faucibus. Fusce aliquet faucibus ultricies. Morbi semper,</p>
  </section>

  <p class="closing">Sincerely,</p>
  <div class="signature" role="img" aria-label="Handwritten signature of the sender"></div>

  <div class="footer-band">
    <div class="footer-band-red"></div>
    <div class="footer-band-grey"></div>
  </div>
</main>
</body>
</html>
```